Business Cards

Need business card design that I can update for new employees and details. Needs to incorporate our logo, be bright and fun (in line with tourism and holidays)
Would like a Map of Western Australia on the front with locations all the caravan parks we own (just purchased Tom Price so please include that as well as others listed on our website).
Target Market(s)
Famillies
Contact Information for Business Card
5 Cards -
Neil Perrow (Director) e: perrow@wattlebay.com.au p: 0491 570 156
Mira Perrow (Director) e: perrow@wattlebay.com.au p: 0491 570 157
Owen Halvey (General Manager) e: halvey@wattlebay.com.au p: 0491 570 158
Helen Halvey (General Manager) e: halvey@wattlebay.com.au p: 0491 570 159
Colin Danby (Training and Operations Manager) - e: danby@wattlebay.com.au p:0491 570 110
Colors
Look and feel

```html
<!DOCTYPE html>
<html lang="en">
<head>
<meta charset="utf-8">
<title>Wattle Bay Tourist Parks – Business Card</title>
<link href="https://fonts.googleapis.com/css2?family=Roboto:wght@400;500&family=Roboto+Condensed:wght@500&display=swap" rel="stylesheet">
<style>
  :root {
    --bg: #e9e7e3;
    --card-white: #fbfbfb;
    --teal: #00bccb;
    --teal-deep: #14a9b5;
    --ink: #3a3a3a;
    --ink-soft: #4a4a4a;
    --white: #ffffff;
  }
  * { margin: 0; padding: 0; box-sizing: border-box; }
  html, body {
    width: 1200px; height: 800px; overflow: hidden;
    background: var(--bg);
    font-family: "Roboto", Arial, sans-serif;
  }
  .canvas {
    position: relative; width: 1200px; height: 800px;
    display: flex; align-items: center; justify-content: center; gap: 40px;
  }
  .card {
    position: relative; width: 530px; height: 303px;
    border-radius: 4px; overflow: hidden;
    box-shadow: 0 6px 18px rgba(0,0,0,0.12);
  }

  /* Front */
  .card--front { background: var(--card-white); }
  .card__tab {
    position: absolute; right: 0; top: 18px;
    width: 9px; height: 40px; background: var(--teal);
    border-radius: 6px 0 0 6px;
  }
  .person {
    position: absolute; right: 38px; top: 34px; text-align: right;
    font-family: "Roboto Condensed", "Arial Narrow", sans-serif; font-weight: 500;
    color: var(--teal-deep);
  }
  .person__name { font-size: 23px; letter-spacing: 0.2px; }
  .person__role { font-size: 15px; margin-top: 2px; }

  .brand {
    position: absolute; left: 48px; top: 108px;
    display: flex; align-items: center; gap: 14px;
    color: var(--ink); font-weight: 400;
  }
  .brand__square { width: 46px; height: 46px; background: var(--teal); flex: none; }
  .brand__name { font-size: 27px; letter-spacing: 5px; text-transform: uppercase; line-height: 1; }
  .brand__sub { font-size: 12px; letter-spacing: 5px; text-transform: uppercase; margin-top: 6px; }

  .contacts {
    position: absolute; left: 48px; bottom: 34px;
    list-style: none; color: var(--ink-soft); font-size: 15px; line-height: 1.45;
  }
  .contacts li { display: flex; align-items: center; gap: 10px; }
  .contacts svg { width: 13px; height: 13px; flex: none; fill: var(--teal); }

  /* Back */
  .card--back {
    background: var(--teal); color: var(--white);
    display: flex; flex-direction: column; align-items: center; justify-content: center;
  }
  .back-brand { display: flex; align-items: center; gap: 14px; font-weight: 400; }
  .back-brand__square { width: 40px; height: 40px; border: 3px solid var(--white); }
  .back-brand__name { font-size: 26px; letter-spacing: 5px; text-transform: uppercase; }
  .back-web { margin-top: 44px; font-size: 14px; letter-spacing: 3.5px; }
</style>
</head>
<body>
<main class="canvas">
  <section class="card card--front">
    <span class="card__tab"></span>
    <div class="person">
      <div class="person__name">NEIL PERROW</div>
      <div class="person__role">DIRECTOR</div>
    </div>
    <div class="brand">
      <span class="brand__square"></span>
      <div>
        <div class="brand__name">Wattle Bay</div>
        <div class="brand__sub">Tourist Parks</div>
      </div>
    </div>
    <ul class="contacts">
      <li>
        <svg viewBox="0 0 24 24"><path d="M6.6 10.8a15.1 15.1 0 0 0 6.6 6.6l2.2-2.2c.3-.3.7-.4 1-.2 1.1.4 2.3.6 3.6.6.6 0 1 .4 1 1V20c0 .6-.4 1-1 1C10.6 21 3 13.4 3 4c0-.6.4-1 1-1h3.5c.6 0 1 .4 1 1 0 1.3.2 2.5.6 3.6.1.3 0 .7-.2 1z"/></svg>
        0491 570 156
      </li>
      <li>
        <svg viewBox="0 0 24 24"><path d="M2 5h20v14H2z M4 7v.3l8 5 8-5V7z" fill-rule="evenodd"/></svg>
        perrow@wattlebay.com.au
      </li>
      <li>
        <svg viewBox="0 0 24 24"><circle cx="12" cy="12" r="10"/></svg>
        www.wattlebay.com.au
      </li>
    </ul>
  </section>

  <section class="card card--back">
    <div class="back-brand">
      <span class="back-brand__square"></span>
      <span class="back-brand__name">Wattle Bay</span>
    </div>
    <div class="back-web">www.wattlebay.com.au</div>
  </section>
</main>
</body>
</html>
```